Business Cards for a law firm

Business cards for our law firm. Use our silhoette logo and OAK PARTNERS - check our website (www.oakpartners.example)

Contact Information for Business Card

our silhouette logo, OAK PARTNERS, 800-555-0147, Dorian Pemberton, dorian@oakpartners.example

Requirements
Must have
• our silhouette logo, OAK PARTNERS, 800-555-0147, Dorian Pemberton, dorian@oakpartners.example

```html
<!DOCTYPE html>
<html lang="en">
<head>
<meta charset="utf-8">
<title>Oak Partners — Business Cards</title>
<link rel="stylesheet" href="https://fonts.googleapis.com/css2?family=Montserrat:wght@400;500;600;700&display=swap">
<style>
  :root {
    --backdrop: #4a4d4e;
    --card: #1e1e1f;
    --navy: #27316d;
    --gold: #e8a21e;
    --muted: #8b8b8b;
    --figure-top: #232324;
    --figure-bottom: #1a1a1b;
  }
  * { margin: 0; padding: 0; box-sizing: border-box; }
  html, body {
    width: 1200px; height: 1168px; overflow: hidden;
    background: var(--backdrop);
    font-family: "Montserrat", sans-serif;
  }
  .card {
    position: absolute; left: 246px;
    width: 701px; height: 400px;
    background: var(--card);
    border-left: 3px solid var(--gold);
    border-bottom: 3px solid var(--gold);
    box-shadow: 6px 8px 18px rgba(0,0,0,.35);
  }
  .card--front { top: 137px; }
  .card--back { top: 611px; }

  .brand { display: flex; align-items: center; gap: 10px; color: var(--navy); font-weight: 700; position: absolute; }
  .brand__mark { background: var(--navy); }
  .brand--header { left: 30px; top: 40px; font-size: 26px; letter-spacing: .5px; }
  .brand--header .brand__mark { width: 22px; height: 22px; }
  .brand--center { left: 0; right: 0; top: 168px; justify-content: center; font-size: 38px; letter-spacing: .5px; }
  .brand--center .brand__mark { width: 32px; height: 32px; }

  .figures {
    position: absolute; left: 338px; top: 90px; width: 188px; height: 284px;
    background: linear-gradient(180deg, var(--figure-top), var(--figure-bottom));
    border-radius: 40px 40px 6px 6px;
  }

  .details { position: absolute; left: 30px; top: 183px; }
  .details__firm { color: var(--navy); font-weight: 700; font-size: 22px; line-height: 1; }
  .details__tagline { color: var(--muted); font-size: 12px; font-weight: 500; letter-spacing: 4.6px; margin-top: 8px; }
  .details__rule { width: 22px; height: 2px; background: var(--gold); margin-top: 18px; }
  .details__name { color: var(--muted); font-size: 18px; font-weight: 500; letter-spacing: 1px; margin-top: 22px; line-height: 1.15; }
  .details__role { color: var(--muted); font-size: 15px; font-weight: 500; letter-spacing: 1px; }
  .contact { list-style: none; margin-top: 22px; }
  .contact__item { display: flex; align-items: center; gap: 10px; color: var(--muted); font-size: 13px; letter-spacing: 1.5px; height: 24px; }
  .contact__icon { width: 17px; height: 17px; flex: none; fill: var(--gold); }
</style>
</head>
<body>
  <section class="card card--front" aria-label="Card front">
    <div class="brand brand--header"><span class="brand__mark"></span>OAK PARTNERS</div>
    <div class="figures" role="img" aria-label="Blind-embossed silhouettes of two standing men in suits"></div>
    <div class="details">
      <p class="details__firm">OAK PARTNERS</p>
      <p class="details__tagline">INJURY ATTORNEYS</p>
      <div class="details__rule"></div>
      <p class="details__name">DORIAN PEMBERTON</p>
      <p class="details__role">ATTORNEY</p>
      <ul class="contact">
        <li class="contact__item">
          <svg class="contact__icon" viewBox="0 0 24 24" aria-hidden="true"><path d="M6.6 10.8c1.4 2.8 3.8 5.1 6.6 6.6l2.2-2.2c.3-.3.7-.4 1-.2 1.1.4 2.3.6 3.6.6.6 0 1 .4 1 1V20c0 .6-.4 1-1 1C10.6 21 3 13.4 3 4c0-.6.4-1 1-1h3.5c.6 0 1 .4 1 1 0 1.3.2 2.5.6 3.6.1.3 0 .7-.2 1z"/></svg>
          800-555-0147
        </li>
        <li class="contact__item">
          <svg class="contact__icon" viewBox="0 0 24 24" aria-hidden="true"><path d="M2 5h20v2l-10 6L2 7z M2 9l10 6 10-6v10H2z"/></svg>
          www.oakpartners.example
        </li>
      </ul>
    </div>
  </section>

  <section class="card card--back" aria-label="Card back">
    <div class="brand brand--center"><span class="brand__mark"></span>OAK PARTNERS</div>
  </section>
</body>
</html>
```